BOLD & MINIMALIST DESIGN NEEDED

We want a very bold but minimalistic business card design that is impactful and utilizes both sides of the business card. Our current logo is included for your use.

We want bold fonts and good use of negative space. We don't want the logo to overpower the design.

Target Market(s)

Professionals who are building new commercial buildings.

Industry/Entity Type

Construction

Contact Information for Business Card

Name, Title, email, office phone, cell phone, website

Font styles to use
Serif
Sans Serif

Requirements
Must have
• Bold design!

```html
<!DOCTYPE html>
<html lang="en">
<head>
<meta charset="utf-8">
<title>Ridgeway Design + Build — Business Card</title>
<link href="https://fonts.googleapis.com/css2?family=Montserrat:wght@400;500;800&display=swap" rel="stylesheet">
<style>
  :root {
    --backdrop: #2a2a2a;
    --card-white: #ffffff;
    --brand-green: #84c441;
    --brand-green-dark: #6aa52f;
    --ink: #111111;
    --text: #222222;
  }
  * { box-sizing: border-box; margin: 0; padding: 0; }
  html, body {
    width: 1200px; height: 900px; overflow: hidden;
    background: var(--backdrop);
    font-family: "Montserrat", sans-serif;
  }
  .sheet {
    position: relative; width: 1200px; height: 900px;
    display: flex; flex-direction: column; align-items: center; justify-content: center; gap: 60px;
  }
  .card {
    position: relative; width: 560px; height: 320px;
    border-radius: 22px; overflow: hidden;
    box-shadow: 0 14px 30px rgba(0,0,0,.45);
  }
  /* Front */
  .card--front { background: var(--card-white); }
  .card__wave { position: absolute; inset: 0; }
  .brand {
    position: absolute; left: 46px; top: 78px; width: 230px;
    display: flex; align-items: center; gap: 10px;
  }
  .brand__mark { width: 22px; height: 22px; background: var(--brand-green); flex: none; }
  .brand__name {
    font-weight: 800; font-size: 21px; line-height: 1.1; color: var(--ink);
    text-transform: uppercase; letter-spacing: .5px;
  }
  .divider {
    position: absolute; left: 300px; top: 58px; width: 2px; height: 150px;
    background: var(--brand-green);
  }
  .contact { position: absolute; left: 322px; top: 56px; color: var(--text); }
  .contact__name {
    font-weight: 800; font-size: 22px; color: var(--brand-green);
    text-transform: uppercase; letter-spacing: .5px;
  }
  .contact__title { font-weight: 500; font-size: 12px; text-transform: uppercase; margin: 2px 0 8px; }
  .contact__address { font-size: 12px; line-height: 1.4; margin-bottom: 6px; }
  .contact__list { list-style: none; font-size: 12px; line-height: 1.55; }
  .contact__list li { display: flex; align-items: center; gap: 7px; }
  .contact__icon { width: 11px; height: 11px; flex: none; fill: var(--brand-green); }
  /* Back */
  .card--back {
    background: linear-gradient(135deg, #8fcb4f 0%, var(--brand-green) 55%, #7ab93a 100%);
    display: flex; align-items: center; justify-content: center;
  }
  .back-brand { display: flex; align-items: center; gap: 16px; }
  .back-brand__mark { width: 34px; height: 34px; background: var(--brand-green-dark); }
  .back-brand__name {
    font-weight: 800; font-size: 34px; color: var(--brand-green-dark);
    text-transform: uppercase; letter-spacing: 1px; line-height: 1.1;
  }
</style>
</head>
<body>
<main class="sheet">
  <section class="card card--front" aria-label="Card front">
    <svg class="card__wave" viewBox="0 0 560 320" preserveAspectRatio="none" aria-hidden="true">
      <path d="M0 120 C140 140 220 250 340 290 C420 316 500 316 560 300 L560 320 L0 320 Z" fill="var(--brand-green)"/>
      <path d="M0 112 C140 132 220 242 340 282 C420 308 500 306 560 290" fill="none" stroke="var(--ink)" stroke-width="5"/>
      <path d="M0 122 C140 142 220 252 340 292 C420 318 500 316 560 302" fill="none" stroke="var(--card-white)" stroke-width="4"/>
    </svg>
    <div class="brand">
      <span class="brand__mark"></span>
      <span class="brand__name">Ridgeway<br>Design + Build</span>
    </div>
    <div class="divider"></div>
    <div class="contact">
      <p class="contact__name">Marcus Bell</p>
      <p class="contact__title">Owner-CEO</p>
      <p class="contact__address">Your address, City<br>State, Zip 1234</p>
      <ul class="contact__list">
        <li><svg class="contact__icon" viewBox="0 0 12 12"><path d="M1 3c0-1 1-2 2-2l1.5 2.5L3.5 5c.8 1.6 1.9 2.7 3.5 3.5l1.5-1L11 9c0 1-1 2-2 2C4.6 11 1 7.4 1 3z"/></svg>123 456 789</li>
        <li><svg class="contact__icon" viewBox="0 0 12 12"><rect x="3" y="0.5" width="6" height="11" rx="1.2"/></svg>123 456 789</li>
        <li><svg class="contact__icon" viewBox="0 0 12 12"><path d="M0.5 2.5h11v7h-11z M0.5 2.5l5.5 4 5.5-4" stroke="#fff" stroke-width=".6"/></svg>info@yourgmail.com</li>
        <li><svg class="contact__icon" viewBox="0 0 12 12"><circle cx="6" cy="6" r="5.5"/></svg>www.yourwebsite.com</li>
      </ul>
    </div>
  </section>

  <section class="card card--back" aria-label="Card back">
    <div class="back-brand">
      <span class="back-brand__mark"></span>
      <span class="back-brand__name">Ridgeway<br>Design + Build</span>
    </div>
  </section>
</main>
</body>
</html>
```